Home Page Enhancement

I am upgrading an existing site and have had a designer help me to create a new look and feel. Whilst I am generally happy with it, I am still not happy with the top half of the page, more specifically the background image on the search box.

I am therefore looking for someone clever and creative to improve on this.

Please see attached files of the new design, plus two examples that could potentially work as improvements.

Target Market(s)

Korean travelers looking to find the best deals and lowest prices on their next hotel stay

Requirements
Must have
• Must emphasise the search box so users are naturally drawn to the search box to initiate a search.
Nice to have
• The background image could potentially emphasize the overall value proposition of the site which is about searching hundreds of travel sites in one search to find you the very best deals.

```html
<!DOCTYPE html>
<html lang="en">
<head>
<meta charset="UTF-8">
<title>StayScout – Hotel Search</title>
<link rel="stylesheet" href="https://fonts.googleapis.com/css2?family=PT+Sans:wght@400;700&display=swap">
<style>
  :root {
    --sky-top: #1c5fb6;
    --sky-mid: #1f7cc2;
    --sea: #1d8a9a;
    --shore: #1e6e48;
    --bar-top: #0b5bb0;
    --bar-bottom: #053a7c;
    --bar-edge: #2a78c8;
    --panel-top: #1eaaea;
    --panel-bottom: #0e92d2;
    --panel-rule: #5ec6f2;
    --panel-edge: #62c9f4;
    --white: #ffffff;
    --highlight: #fff200;
    --field-top: #ffffff;
    --field-bottom: #e4e6e8;
    --field-border: #9fb4c4;
    --field-text: #333a40;
    --select-arrow: #0b4a83;
    --calendar: #4a5a78;
    --button-top: #2cb0f2;
    --button-bottom: #0a72cc;
    --button-text: #0b2a4a;
    --social-a: #4caf50;
    --social-b: #3b5d9a;
    --social-c: #3aa0dc;
    --social-d: #d2456e;
  }

  * { box-sizing: border-box; margin: 0; padding: 0; }

  html, body {
    width: 1200px;
    height: 501px;
    overflow: hidden;
  }

  body {
    position: relative;
    font-family: "PT Sans", Arial, sans-serif;
    color: var(--white);
  }

  .hero-backdrop {
    position: absolute;
    inset: 0;
    background: linear-gradient(180deg, var(--sky-top) 0%, var(--sky-mid) 50%, var(--sea) 78%, var(--shore) 100%);
  }

  .site-header {
    position: absolute;
    left: 120px;
    top: 23px;
    width: 960px;
    height: 52px;
    background: linear-gradient(180deg, var(--bar-top), var(--bar-bottom));
    border: 1px solid var(--bar-edge);
  }

  .brand-name {
    position: absolute;
    left: 11px;
    top: 8px;
    font-size: 27px;
    font-weight: 700;
    letter-spacing: 2px;
    color: var(--white);
  }

  .social-links {
    position: absolute;
    right: 12px;
    top: 24px;
    display: flex;
    gap: 5px;
  }

  .social-links span {
    width: 15px;
    height: 15px;
    border-radius: 2px;
  }
  .social-links .s1 { background: var(--social-a); }
  .social-links .s2 { background: var(--social-b); }
  .social-links .s3 { background: var(--social-c); }
  .social-links .s4 { background: var(--social-d); }

  .search-panel {
    position: absolute;
    left: 116px;
    top: 166px;
    width: 605px;
    height: 281px;
    border-radius: 12px;
    background: linear-gradient(180deg, var(--panel-top), var(--panel-bottom));
    border: 1px solid var(--panel-edge);
    box-shadow: 0 2px 8px rgba(0, 30, 70, 0.35);
  }

  .search-title {
    height: 48px;
    padding: 7px 0 0 14px;
    font-size: 25px;
    font-weight: 700;
    white-space: nowrap;
    border-bottom: 1px solid var(--panel-rule);
  }
  .search-title em { font-style: normal; color: var(--highlight); }

  .field-label {
    position: absolute;
    font-size: 18px;
    font-weight: 700;
    line-height: 1;
  }

  .field {
    position: absolute;
    height: 33px;
    border-radius: 5px;
    border: 1px solid var(--field-border);
    background: linear-gradient(180deg, var(--field-top), var(--field-bottom));
    color: var(--field-text);
    font-size: 12.5px;
    line-height: 31px;
    padding-left: 9px;
    white-space: nowrap;
  }

  .field svg {
    position: absolute;
    right: 5px;
    top: 5px;
  }

  .opt-in {
    position: absolute;
    left: 17px;
    top: 201px;
    display: flex;
    align-items: center;
    gap: 9px;
    font-size: 12px;
  }

  .opt-in .checkbox {
    width: 16px;
    height: 16px;
    border-radius: 2px;
    background: var(--white);
    border: 1px solid var(--field-border);
  }

  .submit-button {
    position: absolute;
    left: 17px;
    top: 234px;
    width: 72px;
    height: 33px;
    border-radius: 8px;
    background: linear-gradient(180deg, var(--button-top), var(--button-bottom));
    border: 1px solid #54c2f4;
    color: var(--button-text);
    font-size: 15px;
    font-weight: 700;
    text-align: center;
    line-height: 31px;
  }
</style>
</head>
<body>
  <div class="hero-backdrop" role="img" aria-label="Photograph of a tropical beach resort under a blue sky"></div>

  <header class="site-header">
    <div class="brand-name">STAYSCOUT</div>
    <nav class="social-links" aria-label="Social links">
      <span class="s1"></span><span class="s2"></span><span class="s3"></span><span class="s4"></span>
    </nav>
  </header>

  <section class="search-panel">
    <h1 class="search-title">Lorem ipsum dolor sit ipsum dolor <em>50%</em> sit ipsum</h1>

    <div class="field-label" style="left:15px; top:63px;">Where</div>
    <div class="field" style="left:14px; top:82px; width:274px;">Lorem ipsum</div>
    <div class="field" style="left:308px; top:82px; width:274px;">Lorem ipsum</div>

    <div class="field-label" style="left:15px; top:132px;">When</div>
    <div class="field-label" style="left:314px; top:132px;">Rooms</div>
    <div class="field-label" style="left:453px; top:132px;">Guests</div>

    <div class="field" style="left:14px; top:151px; width:132px; height:34px;">01/12/2013
      <svg width="20" height="20" viewBox="0 0 20 20" aria-hidden="true"><rect x="2" y="4" width="16" height="14" rx="2" fill="none" stroke="var(--calendar)" stroke-width="1.6"/><rect x="2" y="4" width="16" height="4" fill="var(--calendar)"/><line x1="6" y1="2" x2="6" y2="6" stroke="var(--calendar)" stroke-width="1.6"/><line x1="14" y1="2" x2="14" y2="6" stroke="var(--calendar)" stroke-width="1.6"/><g fill="var(--calendar)"><rect x="5" y="10" width="2" height="2"/><rect x="9" y="10" width="2" height="2"/><rect x="13" y="10" width="2" height="2"/><rect x="5" y="14" width="2" height="2"/><rect x="9" y="14" width="2" height="2"/><rect x="13" y="14" width="2" height="2"/></g></svg>
    </div>
    <div class="field" style="left:156px; top:151px; width:132px; height:34px;">01/01/2013
      <svg width="20" height="20" viewBox="0 0 20 20" aria-hidden="true"><rect x="2" y="4" width="16" height="14" rx="2" fill="none" stroke="var(--calendar)" stroke-width="1.6"/><rect x="2" y="4" width="16" height="4" fill="var(--calendar)"/><line x1="6" y1="2" x2="6" y2="6" stroke="var(--calendar)" stroke-width="1.6"/><line x1="14" y1="2" x2="14" y2="6" stroke="var(--calendar)" stroke-width="1.6"/><g fill="var(--calendar)"><rect x="5" y="10" width="2" height="2"/><rect x="9" y="10" width="2" height="2"/><rect x="13" y="10" width="2" height="2"/><rect x="5" y="14" width="2" height="2"/><rect x="9" y="14" width="2" height="2"/><rect x="13" y="14" width="2" height="2"/></g></svg>
    </div>

    <div class="field" style="left:308px; top:151px; width:132px; height:34px;">1
      <svg width="22" height="22" viewBox="0 0 22 22" aria-hidden="true"><rect width="22" height="22" rx="2" fill="var(--select-arrow)"/><polyline points="6,8 11,14 16,8" fill="none" stroke="var(--white)" stroke-width="2.6"/></svg>
    </div>
    <div class="field" style="left:450px; top:151px; width:132px; height:34px;">2guests
      <svg width="22" height="22" viewBox="0 0 22 22" aria-hidden="true"><rect width="22" height="22" rx="2" fill="var(--select-arrow)"/><polyline points="6,8 11,14 16,8" fill="none" stroke="var(--white)" stroke-width="2.6"/></svg>
    </div>

    <label class="opt-in"><span class="checkbox"></span>Lorem ipsum text here</label>

    <div class="submit-button">Submit</div>
  </section>
</body>
</html>
```